Online Banner and skyscrapper ads

Design ads for real estate company in Australia to be used on Nest huntr.com.au details below
sizes
Leaderboard Specifications
• Dimensions: 728×90px
• Format: HTML5 or Animated/Static Gif
• Max file size: 100kb (HTML5), 80kb (GIF, JPG, PNG)
• Back-up image: 40kb (GIF, JPG, PNG). Back-up image only required if you supply an HTML5 banner.
• Looping: Yes
• See Leaderboard for more information.
Email Alert Strip Ad (EASA) Specifications
• Dimensions: 472×114 px
• Format: JPEG, PNG or Static GIF
• File Size: 20kb
• Looping: No
Skyscraper Specifications
• Dimensions: 160x600px
• Looping: Yes
• See Skyscraper for more information.
Mega Skyscraper Specifications
• Dimensions: 300x600px
• Format: HTML5 or Animated/Static GIF
• File size: 100kb (Html5) or 80kb (GIF, JPG, PNG)
• Back-up image: 40kb (JPG or PNG). Back-up image only required if you supply an HTML5 banner.
• Looping: Yes
• See Half Page for more information.

I would like them to be quite simple , TREVANCE Your Faulconbridge property experts and another saying TREVANCE your Lawson property experts and TREVANCE your Hazelbrook property experts (3 different versions all up ) and another version MOIRA DELVINE your Faulconbridge property expert with logo and her image , i've put a photo of the top banner example and a video of the side banner it has a video in the background that i will get produced if it works

```html
<!DOCTYPE html>
<html lang="en">
<head>
<meta charset="utf-8">
<title>TREVANCE Skyscraper Ads</title>
<link rel="stylesheet" href="https://fonts.googleapis.com/css2?family=Montserrat:wght@400;500&display=swap">
<style>
  :root {
    --page-bg: #ffffff;
    --sky-top: #5b6277;
    --sky-mid: #6a7188;
    --horizon: #3b4359;
    --forest: #1d2535;
    --forest-deep: #131a25;
    --ink-light: #f2f3f6;
    --ink-soft: #c4c8d3;
  }
  * { box-sizing: border-box; margin: 0; padding: 0; }
  html, body {
    width: 1200px;
    height: 546px;
    overflow: hidden;
    background: var(--page-bg);
    font-family: "Montserrat", Arial, sans-serif;
  }
  .ad-row {
    position: relative;
    width: 1200px;
    height: 546px;
  }
  .skyscraper {
    position: absolute;
    top: 65px;
    width: 89px;
    height: 333px;
    overflow: hidden;
    box-shadow: 2px 2px 5px rgba(0, 0, 0, 0.25);
  }
  .skyscraper--faulconbridge { left: 165px; }
  .skyscraper--hazelbrook { left: 565px; }
  .skyscraper--lawson { left: 964px; }

  .skyscraper__backdrop {
    position: absolute;
    inset: 0;
    background: linear-gradient(
      to bottom,
      var(--sky-top) 0%,
      var(--sky-mid) 18%,
      var(--horizon) 30%,
      var(--forest) 42%,
      var(--forest-deep) 100%
    );
  }
  .brand-name {
    position: absolute;
    left: 0;
    right: 0;
    top: 153px;
    text-align: center;
    font-size: 12px;
    font-weight: 500;
    line-height: 1;
    color: var(--ink-light);
  }
  .tagline {
    position: absolute;
    left: 0;
    right: 0;
    top: 193px;
    text-align: center;
    color: var(--ink-light);
  }
  .tagline__suburb {
    font-size: 6px;
    font-weight: 400;
    line-height: 1;
    color: var(--ink-soft);
  }
  .tagline__headline {
    margin-top: 5px;
    font-weight: 500;
    line-height: 1;
  }
  .tagline__headline span { display: block; }
  .tagline__big { font-size: 16px; }
  .tagline__small { font-size: 13px; margin-top: 2px; }
</style>
</head>
<body>
<main class="ad-row">

  <section class="skyscraper skyscraper--faulconbridge" aria-label="TREVANCE Faulconbridge skyscraper ad">
    <div class="skyscraper__backdrop" role="img" aria-label="Background video: overcast sky above a dark Blue Mountains forest"></div>
    <p class="brand-name">TREVANCE</p>
    <div class="tagline">
      <p class="tagline__suburb">Your Faulconbridge</p>
      <p class="tagline__headline"><span class="tagline__big">Property</span><span class="tagline__small">Experts</span></p>
    </div>
  </section>

  <section class="skyscraper skyscraper--hazelbrook" aria-label="TREVANCE Hazelbrook skyscraper ad">
    <div class="skyscraper__backdrop" role="img" aria-label="Background video: overcast sky above a dark Blue Mountains forest"></div>
    <p class="brand-name">TREVANCE</p>
    <div class="tagline">
      <p class="tagline__suburb">Your Hazelbrook</p>
      <p class="tagline__headline"><span class="tagline__big">Property</span><span class="tagline__small">Experts</span></p>
    </div>
  </section>

  <section class="skyscraper skyscraper--lawson" aria-label="TREVANCE Lawson skyscraper ad">
    <div class="skyscraper__backdrop" role="img" aria-label="Background video: overcast sky above a dark Blue Mountains forest"></div>
    <p class="brand-name">TREVANCE</p>
    <div class="tagline">
      <p class="tagline__suburb">Your Lawson</p>
      <p class="tagline__headline"><span class="tagline__big">Property</span><span class="tagline__small">Experts</span></p>
    </div>
  </section>

</main>
</body>
</html>
```